Create a Dynamic Website for Roadhaven 41Ter!

Dear designers,
We have an exciting design opportunity for you on PixelBazaar. We are in need of a creative and professional website design for our company, Roadhaven 41Ter. Our current website is outdated and fails to convey the image we want to project. We are determined to revamp our online presence and create a website that truly represents who we are.
Roadhaven 41Ter is a versatile establishment offering a Velko Express, sandwich bar, restaurant, parking facilities, and meeting rooms. Each of these aspects deserves its own spotlight on our website. Therefore, we are seeking a WordPress-based website design that allows us to easily make changes, modify texts, and add new content as needed.
It is crucial that the design aligns seamlessly with our new branding and style. We invite you to explore our Instagram (@Roadhaven41ter) and Facebook (@Roadhaven) pages to gain an understanding of our branding and incorporate those elements into the design.
You can find our current website at www.guardedroadhaven.eu, but we want a new website that is vibrant, dynamic, and includes moving elements if possible. We believe this will enhance the user experience and keep visitors engaged for longer periods.
Key elements we would like to include in the new website design are as follows:
Clear presentation of all our services: Velko Express, sandwich bar, restaurant, parking facilities, and meeting rooms.
Easy navigation for visitors to find information effortlessly.
Engaging call-to-action buttons that encourage visitors to take specific actions, such as reserving a meeting room or placing an order.
A dedicated blog section where we can share news, events, and special offers.
Integration of a contact form and contact details for easy communication with our visitors.
Responsive design that works seamlessly across desktop and mobile devices.
We envision a modern and visually appealing website that leaves a lasting positive impression on visitors. We are interested in a design that incorporates creative visual elements and provides a user-friendly interface.
Thank you for your time, and we eagerly await your designs.
Best regards,

```html
<!DOCTYPE html>
<html lang="nl">
<head>
<meta charset="utf-8">
<title>Roadhaven 41Ter — Een thuis ver van huis</title>
<link rel="stylesheet" href="https://fonts.googleapis.com/css2?family=Oswald:wght@500;600;700&family=Poppins:wght@400;500;600;700&display=swap">
<style>
:root{
  --blue:#1b72c2;
  --blue-dark:#145a9e;
  --navy:#232a68;
  --ink:#1f2858;
  --red:#d7141d;
  --text:#3b3f52;
  --grey:#eceef1;
  --white:#ffffff;
}
*{box-sizing:border-box;margin:0;padding:0}
html,body{width:1200px;height:4967px;overflow:hidden}
body{font-family:"Poppins",sans-serif;color:var(--text);background:var(--white);position:relative}
.abs{position:absolute}
.heading{font-family:"Oswald",sans-serif;font-weight:600;color:var(--ink);text-transform:uppercase;line-height:1.05}
.btn-outline{display:inline-block;border:2px solid var(--red);color:var(--ink);font-size:12px;font-weight:600;padding:9px 22px;text-transform:uppercase;background:var(--white);transform:skewX(-12deg)}
.btn-outline span{display:inline-block;transform:skewX(12deg)}

/* Header */
.hero-art{left:0;top:0}
.logo-box{left:92px;top:10px;width:218px;height:96px;background:var(--white);transform:skewX(-12deg);box-shadow:0 4px 12px rgba(0,0,0,.15)}
.logo-text{left:110px;top:38px;width:190px;text-align:center;font-family:"Oswald",sans-serif;font-weight:700;font-size:25px;color:var(--navy);text-transform:uppercase;letter-spacing:.5px}
.topbar{left:570px;top:14px;width:540px;height:40px;background:var(--blue);transform:skewX(-12deg)}
.topbar-social{left:592px;top:28px;display:flex;gap:6px}
.topbar-social i{display:block;width:11px;height:11px;border-radius:50%;background:var(--white)}
.topbar-phone{left:778px;top:25px;color:var(--white);font-size:12px;font-weight:600;display:flex;align-items:center;gap:6px}
.topbar-cta{left:894px;top:14px;width:216px;height:40px;background:var(--red);transform:skewX(-12deg)}
.topbar-cta-text{left:894px;top:26px;width:216px;text-align:center;color:var(--white);font-size:11px;font-weight:600;text-transform:uppercase}
.navbar{left:300px;top:58px;width:800px;height:50px;background:var(--white);transform:skewX(-12deg)}
.nav{left:322px;top:75px;display:flex;gap:25px;align-items:center;font-size:11px;font-weight:500;color:var(--ink);text-transform:uppercase;list-style:none}
.hero-copy{left:85px;top:326px;color:var(--white)}
.hero-title{font-family:"Oswald",sans-serif;font-weight:600;font-size:50px;line-height:1.08;text-transform:uppercase;color:var(--white)}
.hero-sub{font-size:13px;margin-top:12px;line-height:1.55;width:500px}
.btn-red{display:inline-block;background:var(--red);color:var(--white);font-size:12px;font-weight:600;text-transform:uppercase;padding:12px 26px;transform:skewX(-12deg);margin-top:22px}
.btn-red span{display:inline-block;transform:skewX(12deg)}
.mouse{left:590px;top:644px;width:20px;height:32px;border:2px solid var(--white);border-radius:10px}
.mouse::after{content:"";position:absolute;left:7px;top:6px;width:2px;height:7px;background:var(--white);border-radius:2px}

/* About */
.about-shadow{left:88px;top:1220px;width:290px;height:300px;background:linear-gradient(180deg,rgba(0,0,0,.08),rgba(0,0,0,0));}
.about-main{left:160px;top:890px;width:370px;height:510px;background:linear-gradient(135deg,#c28a4f,#2e5a5c 60%,#1d3f45);clip-path:polygon(10% 0,100% 0,90% 100%,0 100%);border-radius:12px}
.about-small{left:340px;top:1166px;width:244px;height:298px;background:var(--white);clip-path:polygon(10% 0,100% 0,90% 100%,0 100%);padding:10px}
.about-small div{width:100%;height:100%;background:linear-gradient(135deg,#d2b184,#c34b2a 45%,#6a8b3a);clip-path:polygon(10% 0,100% 0,90% 100%,0 100%)}
.about-copy{left:617px;top:992px;width:480px}
.about-copy .heading{font-size:42px}
.about-copy p{font-size:12.5px;line-height:1.75;margin-top:12px}
.about-copy .btn-outline{margin-top:22px}

/* Services */
.section-title{width:1200px;left:0;text-align:center;font-size:42px}
.services{left:88px;top:1616px;display:flex;gap:4px}
.service{width:200px;height:258px;background:var(--white);box-shadow:0 10px 22px rgba(0,0,0,.12)}
.service .photo{height:206px;clip-path:polygon(6% 0,100% 0,94% 100%,0 100%)}
.service h3{font-family:"Oswald",sans-serif;font-weight:600;font-size:13px;color:var(--ink);text-align:center;margin-top:16px;text-transform:uppercase}

/* Meetings */
.meet-band{left:0;top:1900px}
.meet-copy{left:123px;top:2216px;width:500px;color:var(--white)}
.meet-copy .heading{color:var(--white);font-size:44px}
.meet-copy p{font-size:12.5px;line-height:1.8;margin-top:10px}
.meet-frame{left:658px;top:2205px;width:300px;height:286px;border:5px solid var(--red);border-radius:18px;transform:skewX(-8deg)}
.feature{background:var(--white);box-shadow:0 12px 24px rgba(0,0,0,.2);transform:skewX(-6deg);display:flex;flex-direction:column;align-items:center;justify-content:center;text-align:center}
.feature span{font-family:"Oswald",sans-serif;font-weight:600;font-size:13px;color:var(--ink);text-transform:uppercase;line-height:1.15;margin-top:14px;display:block}
.f1{left:712px;top:2144px;width:172px;height:212px}
.f2{left:878px;top:2242px;width:172px;height:210px}
.f3{left:700px;top:2372px;width:156px;height:212px}

/* Restaurant */
.rest-intro{left:0;top:2788px;width:1200px;text-align:center;font-size:13px;line-height:1.7}
.rest-photos{left:88px;top:2848px;display:flex;gap:6px}
.rest-photos div{width:340px;height:432px;clip-path:polygon(9% 0,100% 0,91% 100%,0 100%);border-radius:8px}
.rest-arrow{left:1052px;top:3064px;color:var(--white);font-size:16px}
.rest-btns{left:467px;top:3306px;display:flex;gap:10px}

/* Blog */
.blog{left:183px;top:3505px;display:flex;gap:12px}
.post{width:272px;height:362px;background:var(--white);box-shadow:0 10px 22px rgba(0,0,0,.1);transform:skewX(-4deg)}
.post .photo{height:220px;clip-path:polygon(8% 0,100% 0,92% 100%,0 100%)}
.post-body{padding:14px 20px 0 24px;transform:skewX(4deg)}
.post h4{font-family:"Oswald",sans-serif;font-weight:600;font-size:17px;color:var(--ink);text-transform:uppercase}
.post p{font-size:11.5px;line-height:1.5;margin-top:4px}
.post a{display:block;margin-top:6px;color:var(--red);font-size:11.5px;font-weight:700;text-transform:uppercase;text-decoration:none}

/* Instagram */
.insta{left:0;top:3948px;width:1200px;display:flex;justify-content:center;align-items:center;gap:10px}
.insta i{display:block;width:44px;height:44px;border-radius:50%;background:linear-gradient(135deg,#7b3bd0,#e23b6a)}
.insta .heading{font-size:44px}

/* Contact + footer */
.footer-bg{left:0;top:4200px}
.map{left:131px;top:4116px;width:912px;height:406px;background:radial-gradient(circle at 62% 45%,#4b5568,#454a52 45%,#3f4247);clip-path:polygon(5% 0,100% 0,95% 100%,0 100%);border-radius:10px}
.pin{left:744px;top:4312px}
.contact-card{left:231px;top:4058px;width:322px;height:436px;background:var(--white);box-shadow:0 14px 30px rgba(0,0,0,.25);padding:40px 28px}
.contact-card .heading{font-size:30px}
.contact-card p{font-size:11px;line-height:1.45;margin-top:8px;color:var(--ink)}
.field{height:42px;background:var(--grey);margin-top:8px;font-size:12px;color:#666;padding:12px 18px}
.field:first-of-type{margin-top:14px}
.field.tall{height:96px}
.send{margin-top:12px;height:42px;background:var(--red);transform:skewX(-14deg);color:var(--white);font-size:12px;font-weight:700;text-align:center;line-height:42px}
.send span{display:inline-block;transform:skewX(14deg)}
.foot-logo{left:88px;top:4684px;font-family:"Oswald",sans-serif;font-weight:700;font-size:28px;color:var(--white);text-transform:uppercase}
.foot-logo-bar{left:86px;top:4732px;width:210px;height:6px;background:var(--red)}
.foot-col{color:var(--white);font-size:11.5px;line-height:2.2}
.foot-col h5{font-family:"Oswald",sans-serif;font-weight:600;font-size:17px;text-transform:uppercase;line-height:1.2;margin-bottom:8px}
.foot-col ul{list-style:none;line-height:2.15}
.col1{left:403px;top:4638px}
.col2{left:627px;top:4638px}
.col3{left:833px;top:4638px;width:290px;line-height:1.5}
.col3 p{margin-bottom:8px}
.foot-social{display:flex;gap:6px;margin-top:4px}
.foot-social i{display:block;width:11px;height:11px;border:1.5px solid var(--white)}
.foot-rule{left:88px;top:4918px;width:1024px;height:1px;background:rgba(255,255,255,.2)}
.copyright{left:0;top:4932px;width:1200px;text-align:center;color:var(--white);font-size:11.5px}
.to-top{left:1124px;top:4892px;width:42px;height:42px;border-radius:50%;background:var(--blue);display:flex;align-items:center;justify-content:center}
</style>
</head>
<body>

<!-- Hero -->
<svg class="abs hero-art" width="1200" height="870" viewBox="0 0 1200 870" role="img" aria-label="Photo of a driver refuelling a truck at the station pump">
  <defs>
    <linearGradient id="heroFill" x1="0" y1="0" x2="1" y2="0.4">
      <stop offset="0" stop-color="#3e3a37"/>
      <stop offset="0.45" stop-color="#6d6760"/>
      <stop offset="1" stop-color="#b9b5b0"/>
    </linearGradient>
    <linearGradient id="heroShade" x1="0" y1="0" x2="1" y2="0">
      <stop offset="0" stop-color="#000" stop-opacity=".45"/>
      <stop offset=".6" stop-color="#000" stop-opacity="0"/>
    </linearGradient>
  </defs>
  <path d="M0 0H1200V636L140 832Q62 846 42 782L0 640Z" fill="url(#heroFill)"/>
  <path d="M0 0H1200V636L140 832Q62 846 42 782L0 640Z" fill="url(#heroShade)"/>
  <path d="M0 652L36 796Q58 862 146 846L520 776" fill="none" stroke="#1b72c2" stroke-width="11"/>
</svg>

<div class="abs logo-box"></div>
<div class="abs logo-text">Roadhaven 41Ter</div>

<div class="abs topbar"></div>
<div class="abs topbar-social"><i></i><i></i></div>
<div class="abs topbar-phone">
  <svg width="12" height="12" viewBox="0 0 24 24"><path fill="#fff" d="M6.6 10.8a15 15 0 006.6 6.6l2.2-2.2a1 1 0 011-.25 11.4 11.4 0 003.6.57 1 1 0 011 1V20a1 1 0 01-1 1A17 17 0 013 4a1 1 0 011-1h3.5a1 1 0 011 1 11.4 11.4 0 00.57 3.6 1 1 0 01-.25 1z"/></svg>
  014 720 395
</div>
<div class="abs topbar-cta"></div>
<div class="abs topbar-cta-text">Vraag een gesprek aan</div>

<div class="abs navbar"></div>
<ul class="abs nav">
  <li><svg width="14" height="13" viewBox="0 0 24 22"><path fill="#1b72c2" d="M12 1L1 11h3v10h6v-6h4v6h6V11h3z"/></svg></li>
  <li>Over ons</li>
  <li>Broodjesbar</li>
  <li>Restaurant</li>
  <li>Parking</li>
  <li>Seminaries // Feestzaal</li>
  <li>Velko Express</li>
  <li>Contact</li>
</ul>

<div class="abs hero-copy">
  <h1 class="hero-title">Een thuis ver van huis.<br>Roadhaven 41Ter</h1>
  <p class="hero-sub">veelzijdige vestiging met een Velko Express, broodjesbar, restaurant, parkeergelegenheid en vergaderruimtes.</p>
  <a class="btn-red"><span>Vraag een offerte aan</span></a>
</div>
<div class="abs mouse"></div>

<!-- About -->
<div class="abs about-shadow"></div>
<div class="abs about-main" role="img" aria-label="Photo of a staff member serving at the sandwich bar counter"></div>
<div class="abs about-small"><div role="img" aria-label="Photo of a dish with onion rings, salad and dips"></div></div>
<div class="abs about-copy">
  <h2 class="heading">Zoveel meer dan een<br>truckstop.</h2>
  <p>In 2009 ontstond Roadhaven41ter dankzij vier vennoten, met een sterke visie rond veiligheid en comfort voor truckchauffeurs.Anno 2020 zijn het de gebroeders Lemmens die deze visie verder zetten.</p>
  <p>Transport is dan ook onmisbaar in onze huidige maatschappij.</p>
  <p>De gebroeders Lemmens, zelf ook actief in de transportwereld, weten waar de pijnpunten liggen in de sector. Daarom streven zij met Roadhaven41ter een oplossing te bieden op de problematiek rond veiligheid, comfort, hygiëne, parking en degelijke gezonde maaltijden..</p>
  <a class="btn-outline"><span>Lees verder</span></a>
</div>

<!-- Services -->
<h2 class="abs heading section-title" style="top:1544px">Onze diensten</h2>
<div class="abs services">
  <div class="service"><div class="photo" role="img" aria-label="Photo of a cashier at the Velko Express shop" style="background:linear-gradient(135deg,#3a3430,#8a7a6a 50%,#24508a)"></div><h3>Velko Express</h3></div>
  <div class="service"><div class="photo" role="img" aria-label="Photo of a burger" style="background:linear-gradient(135deg,#e0c9a8,#8c4a22 55%,#5a3a20)"></div><h3>Broodjeskraam</h3></div>
  <div class="service"><div class="photo" role="img" aria-label="Photo of the restaurant terrace under tents" style="background:linear-gradient(135deg,#8fb8d6,#d9b98a 55%,#6e5a44)"></div><h3>Restaurant</h3></div>
  <div class="service"><div class="photo" role="img" aria-label="Aerial photo of the truck parking" style="background:linear-gradient(135deg,#8a8e94,#565c64 55%,#9aa0a6)"></div><h3>Parkeermogelijkheden</h3></div>
  <div class="service"><div class="photo" role="img" aria-label="Photo of people seated in a meeting room" style="background:linear-gradient(135deg,#dfe2e6,#b4bbc4 55%,#3d4e6c)"></div><h3>Vergaderzalen</h3></div>
</div>

<!-- Meetings -->
<svg class="abs meet-band" width="1200" height="800" viewBox="0 0 1200 800">
  <defs>
    <linearGradient id="meetFill" x1="0" y1="0" x2="1" y2="1">
      <stop offset="0" stop-color="#1c6fbf"/>
      <stop offset="1" stop-color="#1762ad"/>
    </linearGradient>
  </defs>
  <path d="M0 212L1100 36Q1200 20 1200 110V520Q1190 430 1070 452L0 790Z" fill="url(#meetFill)"/>
</svg>
<div class="abs meet-copy">
  <h2 class="heading">Vergaderen bij<br>Roadhaven 41Ter</h2>
  <p>Zoekt u nog een vergaderzaal? Dan is Roadhaven41ter de perfecte locatie. Wij beschikken over 4 vergaderruimte's met een maximum capaciteit van 70p. Beamer, wifi, whiteboard is allemaal aanwezig.</p>
  <p>Wij verzorgen een volledig drankenpakket met alle soorten frisdranken, waters &amp; koffie. Ook tijdens de lunchpauze bieden wij u verschillende pakketten aan, een broodje of een tas soep of zelfs een volledige menu!</p>
  <p>Indien u hier interesse in heeft kan u altijd bellen naar : &nbsp; + 32 14 555 318</p>
</div>
<div class="abs meet-frame"></div>
<div class="abs feature f1">
  <svg width="64" height="54" viewBox="0 0 64 54" fill="none" stroke="#d7141d" stroke-width="2.4"><circle cx="24" cy="16" r="10"/><path d="M4 50c0-12 9-20 20-20s20 8 20 20z"/><circle cx="44" cy="14" r="8"/><path d="M44 28c9 0 16 7 16 18H48"/></svg>
  <span>Tot 150<br>personen</span>
</div>
<div class="abs feature f2">
  <svg width="76" height="58" viewBox="0 0 76 58" fill="none" stroke="#d7141d" stroke-width="2.4"><path d="M30 4l3 7M38 2v8M46 4l-3 7M24 8l5 5M52 8l-5 5"/><rect x="4" y="20" width="68" height="26" rx="4"/><circle cx="46" cy="33" r="9"/><circle cx="46" cy="33" r="4"/><path d="M12 30h16M12 36h16M10 46v6M66 46v6"/></svg>
  <span>Beamer</span>
</div>
<div class="abs feature f3">
  <svg width="76" height="60" viewBox="0 0 76 60" fill="none" stroke="#d7141d" stroke-width="2.4"><rect x="4" y="4" width="68" height="26" rx="3"/><path d="M10 22h56M50 12h14"/><path d="M24 36v20M16 40l16 12M32 40L16 52M14 46h20" stroke-width="2"/><path d="M46 38c0 6 8 6 8 12M56 38c0 6 8 6 8 12" stroke-width="2"/></svg>
  <span>Airco<br>// verwarming</span>
</div>

<!-- Restaurant -->
<h2 class="abs heading section-title" style="top:2728px">Restaurant</h2>
<p class="abs rest-intro">Ons restaurant is een gezellige warme plek om te vertoeven. Met onze<br>uitgebreide menukaart is er voor ieder wat wils.</p>
<div class="abs rest-photos">
  <div role="img" aria-label="Photo of the terrace tent with tables and benches" style="background:linear-gradient(160deg,#9fbfd8,#d6c4a4 45%,#6b5440)"></div>
  <div role="img" aria-label="Photo of a bowl with glazed meat and fresh vegetables" style="background:linear-gradient(160deg,#3a1c16,#7c2e20 50%,#8fa45a)"></div>
  <div role="img" aria-label="Photo of two guests toasting with drinks at dusk" style="background:linear-gradient(160deg,#2f4a6c,#5f7fa0 50%,#1d2f48)"></div>
</div>
<div class="abs rest-arrow">›</div>
<div class="abs rest-btns">
  <a class="btn-outline"><span>Dagmenu's</span></a>
  <a class="btn-outline"><span>Menukaart</span></a>
</div>

<!-- Blog -->
<h2 class="abs heading section-title" style="top:3434px">Dernier blog</h2>
<div class="abs blog">
  <article class="post"><div class="photo" role="img" aria-label="Photo of a smiling staff member at the counter" style="background:linear-gradient(135deg,#c9c2b8,#3a3433 55%,#6f88a4)"></div><div class="post-body"><h4>Blog heading here</h4><p>Lorem Ipsum has been the industry's standard dummy text ever since the when.</p><a>Read more</a></div></article>
  <article class="post"><div class="photo" role="img" aria-label="Photo of the terrace tents seen from above" style="background:linear-gradient(135deg,#8a9ca8,#d8cbb0 50%,#3f8fa6)"></div><div class="post-body"><h4>Blog heading here</h4><p>Lorem Ipsum has been the industry's standard dummy text ever since the when.</p><a>Read more</a></div></article>
  <article class="post"><div class="photo" role="img" aria-label="Aerial photo of the site with solar roofs" style="background:linear-gradient(135deg,#6f7a80,#a6aca9 50%,#4e6a52)"></div><div class="post-body"><h4>Blog heading here</h4><p>Lorem Ipsum has been the industry's standard dummy text ever since the when.</p><a>Read more</a></div></article>
</div>

<!-- Instagram handle -->
<div class="abs insta"><i></i><span class="heading">@Roadhaven41ter</span></div>

<!-- Footer background -->
<svg class="abs footer-bg" width="1200" height="767" viewBox="0 0 1200 767">
  <path d="M0 250Q60 170 200 150L1200 0V767H0Z" fill="#232a68"/>
</svg>

<!-- Contact -->
<div class="abs map" role="img" aria-label="Dark street map around the location"></div>
<svg class="abs pin" width="24" height="32" viewBox="0 0 24 32"><path d="M12 0C5 0 0 5 0 12c0 9 12 20 12 20s12-11 12-20C24 5 19 0 12 0z" fill="#d7141d"/><circle cx="12" cy="12" r="4.5" fill="#fff"/></svg>
<form class="abs contact-card">
  <h2 class="heading">Contacteer ons</h2>
  <p>Heeft u een opmerking, vraag of suggestie?<br>Laat het ons hier weten.<br>Reserveren kan enkel telefonisch via<br>014 720 395.</p>
  <div class="field">Email *</div>
  <div class="field">Naam *</div>
  <div class="field tall">Bericht *</div>
  <div class="send"><span>Verzenden</span></div>
</form>

<!-- Footer -->
<div class="abs foot-logo">Roadhaven 41Ter</div>
<div class="abs foot-logo-bar"></div>
<div class="abs foot-col col1">
  <h5>Useful links</h5>
  <ul><li>Home</li><li>Over ons</li><li>Broodjesbar</li><li>Restaurant</li><li>Parking</li><li>Seminaries // feestzaal</li><li>Velko express</li><li>Contact</li></ul>
</div>
<div class="abs foot-col col2">
  <h5>Services</h5>
  <ul><li>Velko Express</li><li>Broodjeszaak</li><li>Restaurant</li><li>Parkeergelegenheid</li><li>vergaderzalen</li></ul>
</div>
<div class="abs foot-col col3">
  <h5>Find us!</h5>
  <p>Havenstraat 22<br>3920 Lommelveld</p>
  <p>WORK WITH US!<br>Roadhaven 41Ter staat altijd open om nieuwe talenten te ontdekken.<br>Mail ons: &nbsp;jobs@guardedroadhaven.eu</p>
  <div class="foot-social"><i></i><i></i></div>
</div>
<div class="abs foot-rule"></div>
<div class="abs copyright">©Copyright Guardedroadhaven41ter 2023 | All Rights Reserved</div>
<div class="abs to-top"><svg width="14" height="10" viewBox="0 0 14 10"><path d="M1 8l6-6 6 6" fill="none" stroke="#fff" stroke-width="2"/></svg></div>

</body>
</html>
```